Business Card Design needed for start up company Halvora

In need of a new business card designed for a start up company based in Sydney, Halvora is a new start up innovative Company, our mission it to make property accessible for everyday Australian and to become the leading Real Estate platform in Australia. We want it to be fresh and clean.

Industry/Entity Type

Financial

Contact Information for Business Card

Section for Name
Section for Title

HALVORA - The Strength of Pooling
Mobile:
Direct:

Font styles to use
Sans Serif

Colors
33a6d7
0692cd
0255a3
ffffff

Requirements
Must have
• Logo, all business card details

```html
<!DOCTYPE html>
<html lang="en">
<head>
<meta charset="UTF-8">
<title>Halvora – Business Card</title>
<link href="https://fonts.googleapis.com/css2?family=Open+Sans:wght@400;600;700&display=swap" rel="stylesheet">
<style>
  :root {
    --stage: #000000;
    --card-front: #f3f3f3;
    --sky: #33a6d7;
    --ocean: #0692cd;
    --navy: #0255a3;
    --deep-navy: #1f3f78;
    --ink: #1c1c1c;
    --white: #ffffff;
  }
  * { margin: 0; padding: 0; box-sizing: border-box; }
  html, body {
    width: 1200px; height: 900px; overflow: hidden;
    background: var(--stage);
    font-family: "Open Sans", Arial, sans-serif;
  }
  .stage { position: relative; width: 1200px; height: 900px; }

  .card {
    position: absolute; top: 200px;
    width: 310px; height: 502px;
    overflow: hidden;
  }
  .card--front {
    left: 265px;
    background: var(--card-front);
    border-radius: 60px 0 60px 0;
  }
  .card--back {
    left: 641px; width: 309px;
    background: linear-gradient(180deg, #279cd8 0%, #22669f 55%, var(--deep-navy) 100%);
    border-radius: 0 60px 0 60px;
    color: var(--white);
  }

  .brand {
    position: absolute; left: 21px; top: 62px;
    font-weight: 600; font-size: 38px; line-height: 1;
    letter-spacing: 0.5px;
    color: var(--navy);
  }

  .person { position: absolute; left: 21px; top: 354px; }
  .person__name { font-size: 17px; font-weight: 600; color: var(--navy); line-height: 1.2; }
  .person__title { font-size: 13px; color: var(--ink); line-height: 1.4; }

  .contact { position: absolute; left: 21px; top: 410px; list-style: none; }
  .contact__item {
    display: flex; align-items: center; gap: 8px;
    font-size: 13px; color: var(--ink); height: 20.5px;
  }
  .contact__icon { width: 11px; height: 11px; fill: var(--navy); flex: none; }

  .tagline__line {
    position: absolute; left: 0; width: 100%;
    text-align: center; line-height: 1; font-weight: 600;
    white-space: nowrap;
  }
  .tagline__the { top: 34px; font-size: 136px; }
  .tagline__strength { top: 166px; font-size: 48px; }
  .tagline__of { top: 199px; font-size: 216px; letter-spacing: -6px; }
  .tagline__pooling { top: 403px; font-size: 48px; }
</style>
</head>
<body>
<main class="stage">
  <section class="card card--front" aria-label="Business card front">
    <p class="brand">Halvora</p>
    <div class="person">
      <p class="person__name">Marcus Ellery</p>
      <p class="person__title">Managing Director</p>
    </div>
    <ul class="contact">
      <li class="contact__item">
        <svg class="contact__icon" viewBox="0 0 24 24"><path d="M6.6 10.8a15.1 15.1 0 0 0 6.6 6.6l2.2-2.2c.3-.3.7-.4 1-.2 1.1.4 2.3.6 3.6.6.6 0 1 .4 1 1V20c0 .6-.4 1-1 1A17 17 0 0 1 3 4c0-.6.4-1 1-1h3.5c.6 0 1 .4 1 1 0 1.3.2 2.5.6 3.6.1.3 0 .7-.2 1z"/></svg>
        <span>(02) 9184-3376</span>
      </li>
      <li class="contact__item">
        <svg class="contact__icon" viewBox="0 0 24 24"><path d="M7 1h10a2 2 0 0 1 2 2v18a2 2 0 0 1-2 2H7a2 2 0 0 1-2-2V3a2 2 0 0 1 2-2zm0 3v14h10V4z"/></svg>
        <span>0412-558-230</span>
      </li>
      <li class="contact__item">
        <svg class="contact__icon" viewBox="0 0 24 24"><path d="M2 5h20v14H2zm2 2v.5l8 5 8-5V7l-8 5z"/></svg>
        <span>hello@halvora.com.au</span>
      </li>
    </ul>
  </section>

  <section class="card card--back" aria-label="Business card back">
    <h1 class="tagline">
      <span class="tagline__line tagline__the">THE</span>
      <span class="tagline__line tagline__strength">STRENGTH</span>
      <span class="tagline__line tagline__of">OF</span>
      <span class="tagline__line tagline__pooling">POOLING</span>
    </h1>
  </section>
</main>
</body>
</html>
```